Design a business card
Business name: Harbourline Growth Advisory
Improving Business Profitibility

- An Overview of the Business & Service:

Business Performance Consulting

- The Target Market: Small to medium-sized business

- Design Specifics:
White card, blue ink, moon eclipse

No Logo

Target Market(s)

Small to medium-sized business

Font styles to use
Sans Serif

```html
<!DOCTYPE html>
<html lang="en">
<head>
<meta charset="utf-8">
<title>Harbourline Growth Advisory – Business Card</title>
<link rel="stylesheet" href="https://fonts.googleapis.com/css2?family=Open+Sans:wght@400;600;700&family=Oswald:wght@500&display=swap">
<style>
  :root {
    --stage: #3a3a3a;
    --card-front: #121212;
    --card-back: #000000;
    --green: #5cc51a;
    --blue: #0b4f9c;
    --grey-text: #bfbfbf;
    --name-grey: #9a9a9a;
    --white: #f2f2f2;
    --photo-fill: #9c4525;
  }
  * { box-sizing: border-box; margin: 0; padding: 0; }
  html, body { width: 1200px; height: 782px; overflow: hidden; }
  body {
    background: var(--stage);
    font-family: "Open Sans", Arial, sans-serif;
    position: relative;
  }
  .card {
    position: absolute;
    top: 240px;
    width: 530px;
    height: 303px;
    overflow: hidden;
    box-shadow: 0 10px 24px rgba(0,0,0,0.45);
  }
  .card--front { left: 50px; background: var(--card-front); }
  .card--back { left: 620px; background: var(--card-back); }

  .holder { position: absolute; left: 34px; top: 30px; }
  .holder__name {
    font-family: "Oswald", "Arial Narrow", sans-serif;
    font-weight: 500;
    color: var(--green);
    font-size: 17px;
    letter-spacing: 0.3px;
    text-transform: uppercase;
    line-height: 1.1;
  }
  .holder__title { color: var(--name-grey); font-size: 12px; line-height: 1.3; }

  .contact { position: absolute; left: 34px; top: 148px; list-style: none; }
  .contact li {
    display: flex; align-items: center; gap: 7px;
    color: var(--grey-text); font-size: 12.5px; line-height: 17px;
  }
  .contact svg { width: 10px; height: 10px; fill: var(--green); flex: none; }

  .brand {
    position: absolute; left: 300px; top: 118px;
    color: var(--blue);
    font-weight: 700;
    font-size: 22px;
    line-height: 1.1;
    text-transform: uppercase;
    letter-spacing: 0.5px;
  }

  .address {
    position: absolute; right: 40px; top: 222px;
    color: var(--grey-text); font-size: 13px; line-height: 17px;
  }

  .bands { position: absolute; left: 0; bottom: 0; width: 530px; height: 40px; }

  .photo {
    position: absolute; left: 212px; top: 90px;
    width: 106px; height: 100px;
    background: var(--photo-fill);
  }
  .tagline {
    position: absolute; left: 0; right: 0; top: 206px;
    text-align: center;
    color: var(--white); font-size: 12px; font-weight: 600;
    letter-spacing: 0.4px; text-transform: uppercase;
  }
</style>
</head>
<body>
  <section class="card card--front">
    <div class="holder">
      <p class="holder__name">Desmond R Akerly</p>
      <p class="holder__title">Managing Director</p>
    </div>

    <ul class="contact">
      <li><svg viewBox="0 0 10 10"><path d="M1 2c0-1 1-1.5 2-1.5l1 2-1 1c.6 1.3 1.4 2.1 2.5 2.5l1-1 2 1C8.5 7 8 9 7 9 3.5 9 1 6 1 2z"/></svg>021-480 317 652</li>
      <li><svg viewBox="0 0 10 10"><path d="M3 0h4a1 1 0 0 1 1 1v8a1 1 0 0 1-1 1H3a1 1 0 0 1-1-1V1a1 1 0 0 1 1-1zm0 1.5v6h4v-6z"/></svg>021-480 317 653</li>
      <li><svg viewBox="0 0 10 10"><path d="M0 2h10v6H0zm1 1v.4L5 6l4-2.6V3L5 5.5z"/></svg>hello@harbourline.com</li>
      <li><svg viewBox="0 0 10 10"><circle cx="5" cy="5" r="5"/></svg>www.harbourline.com</li>
    </ul>

    <p class="brand">Harbourline<br>Growth Advisory</p>

    <p class="address">48 Quayside Row, Suite 7<br>Westport, 204519</p>

    <svg class="bands" viewBox="0 0 530 40" aria-hidden="true">
      <polygon points="0,14 268,14 260,30 0,30" fill="var(--blue)"/>
      <polygon points="276,14 530,14 530,40 262,40" fill="var(--green)"/>
    </svg>
  </section>

  <section class="card card--back">
    <div class="photo" role="img" aria-label="Photo placeholder: copper-red eclipsed moon on a black sky"></div>
    <p class="tagline">Improving Business Profitibility</p>
  </section>
</body>
</html>
```